Smart Design for Global Industrial Business

We are commissioned to replace an existing industrial business website with a new website with new branding and layout for CMS / Responsive (Wordpress). The existing website is to be replaced (rvtbindings.com) with one that is more in keeping with the new brand book and modern design standards.
Note that they have two online stores (rvt-gripping.co.uk and .com) and this site will need to fit with those, whilst being very different and much more about RVT and their scope / reach.
Please just design the homepage first as we will try to give everyone a chance to build from there if they are heading in the right direction.
The eventual delivery will be of all the wireframes, in source file format (ideally PSD) as well as PNGs.
We will aim to feedback in detail to all participants, but if you really don't try that hard, it may be brief!

Target Market(s)

Buyers in companies who are looking for clamping / restraining products - to persuade them that these are the best, most reliable, products.

Industry/Entity Type

Industrial safety/banding products

Number of Pages Required

5+ page

Font styles to use
Sans Serif
Other font styles liked:
• see current websites

Requirements
Must have
• A really good consistent level of design with consideration of mobile users and lead generation.
Nice to have
• I just want to see good creative, if possible. Don't try too many things, keep it simple.
Should not have
• No untidiness or lack of consistency.

```html
<!DOCTYPE html>
<html lang="en">
<head>
<meta charset="utf-8">
<title>RVT Fasteners – Clamping and Banding Solutions</title>
<link rel="stylesheet" href="https://fonts.googleapis.com/css2?family=Barlow:wght@300;400;500;600;700&display=swap">
<style>
:root{
  --orange:#f26522;
  --navy:#263647;
  --navy-dark:#1d2b3a;
  --ink:#2f3a45;
  --text:#5b636b;
  --line:#cfd6de;
  --pale:#eef2f6;
  --white:#ffffff;
}
*{box-sizing:border-box;margin:0;padding:0}
html,body{width:1200px;height:4525px;overflow:hidden}
body{font-family:'Barlow',sans-serif;color:var(--text);background:var(--white);position:relative}
a{color:inherit;text-decoration:none}
.wrap{position:relative;width:1200px}

/* top bar */
.topbar{height:30px;background:#f3f5f8;display:flex;justify-content:flex-end;align-items:center;padding-right:60px;font-size:11px;font-weight:600;color:var(--ink)}
.topbar a{padding:0 14px;border-left:1px solid var(--line);line-height:30px}
.topbar a:first-child{border-left:0}

/* header */
.header{height:88px;display:flex;align-items:center;padding:0 0 0 108px;border-bottom:1px solid #e4e8ec}
.brand{display:flex;align-items:center;gap:8px;font-weight:700;font-size:40px;color:var(--navy);letter-spacing:1px;width:214px}
.brand .dot{width:14px;height:14px;border-radius:50%;background:var(--orange)}
.nav{display:flex;gap:0;height:88px}
.nav a{display:flex;align-items:center;padding:0 22px;font-size:14px;font-weight:500;color:var(--ink);position:relative}
.nav a.active{font-weight:700;color:var(--navy)}
.nav a.active::after{content:"";position:absolute;left:22px;right:22px;bottom:0;height:3px;background:var(--orange)}

/* hero */
.hero{height:606px;background:linear-gradient(180deg,#3d4b57 0%,#55646d 35%,#2d3a46 70%,#3b4650 100%);position:relative;color:var(--white);text-align:center}
.hero h1{position:absolute;top:170px;left:0;right:0;font-weight:300;font-size:38px;line-height:48px;letter-spacing:.5px}
.hero h1 strong{display:block;font-weight:700;font-size:44px}
.rule{width:70px;height:4px;background:var(--orange);margin:0 auto}
.hero .rule{position:absolute;top:284px;left:565px}
.hero .arrow{position:absolute;top:238px;width:30px;height:60px}
.hero-btns{position:absolute;top:347px;left:182px;display:flex;gap:6px}
.hero-btns a{width:275px;height:58px;display:flex;align-items:center;justify-content:center;gap:10px;font-size:18px;font-weight:500;background:rgba(29,43,58,.88)}
.hero-btns a.on{background:var(--orange)}

/* about */
.about{height:538px;position:relative}
.about-box{position:absolute;top:114px;left:122px;width:953px;height:345px;border:2px solid #d6dde4;padding:56px 70px 0;text-align:center;font-size:14.5px;line-height:23px}
.about-box p{margin-bottom:22px}
.about-logo{position:absolute;top:80px;left:530px;width:140px;height:60px;background:var(--white);display:flex;align-items:center;justify-content:center;gap:7px;font-weight:700;font-size:34px;color:var(--navy)}
.about-logo .dot{width:11px;height:11px;border-radius:50%;background:var(--orange)}

/* challenge */
.challenge{height:555px;background:linear-gradient(180deg,#d3dce5 0%,#e4ebf1 45%,#cdd8e2 100%);text-align:center;padding-top:92px;color:var(--ink)}
.challenge h2{font-size:34px;font-weight:700;color:var(--navy-dark);line-height:40px}
.challenge h2 span{display:block;font-weight:300;color:var(--navy)}
.challenge .rule{margin:10px auto 30px}
.challenge p{font-size:16px;line-height:19px;width:700px;margin:0 auto 17px}
.select{margin:38px auto 0;width:423px;height:52px;background:#f6f8fa;border:1px solid #d9e0e6;display:flex;align-items:center;justify-content:space-between;padding:0 20px;font-size:15px;color:var(--ink)}

/* custom */
.custom{height:555px;background:linear-gradient(180deg,#2b3f55 0%,#3a5068 40%,#23364a 100%);color:var(--white);text-align:center;padding-top:118px}
.custom h2{font-size:36px;font-weight:300;letter-spacing:.5px}
.custom h2 strong{font-weight:700}
.custom .rule{margin:8px auto 24px}
.custom p{font-size:14.5px;line-height:22px;width:740px;margin:0 auto}
.btn-outline{display:inline-block;margin:18px 0 22px;border:2px solid var(--white);padding:11px 30px;font-size:14px;font-weight:600}
.custom u{text-underline-offset:3px}

/* case studies */
.cases{height:524px;position:relative}
.sec-title{text-align:center;font-size:32px;font-weight:300;color:var(--navy)}
.sec-title strong{font-weight:700}
.cases .sec-title{padding-top:54px}
.sec-title + .rule{margin-top:10px}
.case-row{position:absolute;top:142px;left:105px;display:flex;gap:10px}
.case-frame-a{position:absolute;top:136px;left:97px;width:90px;height:90px;border-top:8px solid var(--navy);border-left:8px solid var(--navy)}
.case-frame-b{position:absolute;top:260px;left:1010px;width:90px;height:96px;border-bottom:8px solid var(--navy);border-right:8px solid var(--navy)}
.case{width:240px;background:var(--white);border:1px solid #dfe4ea;position:relative}
.case .photo{height:208px}
.case .cap{height:70px;padding:22px 24px 0;font-size:14px;font-weight:600;color:var(--ink);line-height:18px;text-transform:uppercase}
.case.on .cap{background:var(--orange);color:var(--white)}

/* news */
.news{height:551px;background:var(--pale);position:relative}
.news .sec-title{padding-top:56px}
.news-row{position:absolute;top:136px;left:98px;display:flex;gap:15px}
.post{width:240px;height:323px;background:var(--white);border:1px solid #cfd8e1}
.post .photo{height:187px;position:relative}
.post .date{position:absolute;left:0;bottom:0;background:var(--orange);color:var(--white);font-size:11px;font-weight:500;padding:3px 8px}
.post h3{font-size:12.5px;font-weight:700;color:var(--ink);line-height:16px;padding:20px 20px 6px;text-transform:uppercase}
.post p{font-size:10px;padding:0 20px;color:#8a9096}
.post .more{display:block;padding:12px 20px 0;font-size:11px;font-weight:700;color:var(--orange)}

/* offices */
.offices{height:705px;position:relative}
.office{position:absolute;top:68px;width:483px;height:548px;background:var(--white);border:1px solid #d7dde3}
.office .map{height:262px}
.office .info{padding:30px 42px 0}
.office h3{border-left:3px solid var(--orange);padding-left:12px;font-size:20px;font-weight:600;color:var(--navy);line-height:24px}
.office h3 span{display:block;font-weight:300;font-size:20px}
.office h4{font-size:14px;font-weight:700;color:var(--ink);margin:20px 0 4px}
.office .line{display:flex;gap:8px;font-size:13px;line-height:23px;color:var(--text)}
.office .line svg{flex:none;margin-top:5px}
.office .corner{position:absolute;right:-6px;bottom:-6px;width:88px;height:95px;border-right:5px solid var(--orange);border-bottom:5px solid var(--orange)}

/* footer */
.footer{height:373px;background:var(--navy);color:#c9d2db;position:relative}
.f-cols{display:flex;padding-left:133px;height:312px}
.f-col{width:254px;padding-top:54px;border-left:1px solid #34485c;padding-left:0;position:relative}
.f-col:first-child{border-left:0}
.f-col h5{font-size:15px;font-weight:700;color:var(--white);border-left:3px solid var(--orange);padding-left:24px;margin-left:-28px;margin-bottom:18px}
.f-col ul{list-style:none;font-size:11.5px;line-height:23px}
.f-col.contact{font-size:11px;line-height:19px}
.f-col.contact b{color:var(--white);font-weight:600}
.f-col.contact u{text-underline-offset:2px}
.social{display:flex;gap:20px;margin-top:18px}
.social span{width:16px;height:16px;border-radius:50%;background:var(--white)}
.f-cols .f-col:nth-child(2){padding-left:0}
.f-bottom{position:absolute;left:0;right:0;bottom:0;height:61px;display:flex;align-items:center;justify-content:space-between;padding:0 138px 0 130px;font-size:11px;color:#98a6b4}
.f-bottom nav{display:flex;gap:14px;color:var(--white)}
</style>
</head>
<body>
<div class="wrap">

  <div class="topbar"><a href="#">NEWS</a><a href="#">ABOUT US</a><a href="#">CONTACT US</a></div>

  <header class="header">
    <a class="brand" href="#"><span class="dot"></span>RVT</a>
    <nav class="nav">
      <a class="active" href="#">HOSE CLAMPS</a>
      <a href="#">BANDINGS &amp; SADDLES</a>
      <a href="#">CUSTOM SOLUTIONS</a>
      <a href="#">APPLICATIONS</a>
      <a href="#">CASE STUDIES</a>
    </nav>
  </header>

  <section class="hero" role="img" aria-label="Photograph of large black pipelines strapped with banding on an industrial site">
    <svg class="arrow" style="left:74px" viewBox="0 0 30 60"><path d="M26 4 L4 30 L26 56" fill="none" stroke="#fff" stroke-width="2"/></svg>
    <svg class="arrow" style="right:74px" viewBox="0 0 30 60"><path d="M4 4 L26 30 L4 56" fill="none" stroke="#fff" stroke-width="2"/></svg>
    <h1>THE LEADING MANUFACTURING AND SUPPLIER OF<strong>CLAMPING AND BANDING SOLUTIONS</strong></h1>
    <div class="rule"></div>
    <div class="hero-btns">
      <a href="#"><svg width="26" height="22" viewBox="0 0 26 22"><ellipse cx="13" cy="11" rx="11" ry="7" fill="none" stroke="#fff" stroke-width="2" transform="rotate(-25 13 11)"/></svg>HOSE CLAMPS</a>
      <a class="on" href="#"><svg width="24" height="24" viewBox="0 0 24 24"><path d="M3 3 L21 21 M21 3 L3 21" stroke="#fff" stroke-width="2.4"/></svg>BANDING</a>
      <a href="#"><svg width="24" height="24" viewBox="0 0 24 24"><circle cx="12" cy="12" r="4" fill="none" stroke="#fff" stroke-width="2"/><circle cx="12" cy="12" r="9" fill="none" stroke="#fff" stroke-width="2" stroke-dasharray="4 3"/></svg>CUSTOM SOLUTIONS</a>
    </div>
  </section>

  <section class="about">
    <div class="about-box">
      <p>RVT Fasteners is one of the world's leading producers and suppliers of clamping systems for commercial and personal use. We manufacture of non-metallic smart polymer hose clamps and clips - including Grip Clip, Loopclamp, Loopchk and a range of tools.</p>
      <p>We also supply a wide range of selected high quality distributed brands from the most recognised and respected brands of hose clamps and clips.</p>
      <p>With warehouses in the US and the UK we are now supplying across the world both standard and custom solutions to deliver long-lasting, reliable and secure clamping and banding solutions. So, please browse our website or contact us if you have a specific requirement, we look forward to hearing from you.</p>
    </div>
    <div class="about-logo"><span class="dot"></span>RVT</div>
  </section>

  <section class="challenge" role="img" aria-label="Soft photograph of a floating pipeline across calm water">
    <h2>WATER. SUN. COLD. SALT. WIND<span>WE'VE GOT IT COVERED</span></h2>
    <div class="rule"></div>
    <p>There are many situations where you need the right solution to make sure that whatever you need to secure is fixed for good</p>
    <p>At RVT our aim is to recommend the best product for your specific situation, regardless of whether it is ours, or another company.</p>
    <p>So select your challenge, and explore the best product(s) to suit your needs.</p>
    <div class="select">Choose a Challenge?<svg width="16" height="10" viewBox="0 0 16 10"><path d="M1 1 L8 8 L15 1" fill="none" stroke="#56616c" stroke-width="2"/></svg></div>
  </section>

  <section class="custom" role="img" aria-label="Photograph of a pier with pilings over dark water">
    <h2><strong>CUSTOM</strong> SOLUTIONS</h2>
    <div class="rule"></div>
    <p>Our specialisation in non-metallic polymer hose clamps, clips and branding means that we supply to specific projects around the world. Discover how we may be able to assist you.</p>
    <a class="btn-outline" href="#">FIND OUT MORE &rsaquo;</a>
    <p>Or, if you prefer, <u>contact our sales team.</u></p>
    <p style="margin-top:14px">They are experienced in helping understand your requirements, and will bring together a full proposal for exactly what you need. This may include any specialist tools and recommendations on installation partners needed to fulfil the project.</p>
  </section>

  <section class="cases">
    <h2 class="sec-title"><strong>CASE STUDIES</strong> &nbsp;RVT PRODUCT IN PLACE</h2>
    <div class="rule"></div>
    <div class="case-frame-a"></div>
    <div class="case-frame-b"></div>
    <div class="case-row">
      <article class="case on"><div class="photo" role="img" aria-label="Black pile wrap on a large pipe" style="background:linear-gradient(180deg,#6f8397,#1e2a36 60%,#40505f)"></div><div class="cap">Pile wrap system<br>Norvale</div></article>
      <article class="case"><div class="photo" role="img" aria-label="Clamp fitted around a concrete pile on site" style="background:linear-gradient(180deg,#5a7080,#8a8f7a 55%,#6b6650)"></div><div class="cap">ICCP<br>Greyhaven</div></article>
      <article class="case"><div class="photo" role="img" aria-label="Subsea cable with attached floats on a quayside" style="background:linear-gradient(180deg,#9ea8ae,#3d4348 55%,#6f7670)"></div><div class="cap">Subsea cable<br>attachment – Marlow Offshore</div></article>
      <article class="case"><div class="photo" role="img" aria-label="Gloved hands fitting a downhole clamp" style="background:linear-gradient(180deg,#8e7b6a,#b9b7b4 50%,#6a5445)"></div><div class="cap">Downhole –<br>Andara</div></article>
    </div>
  </section>

  <section class="news">
    <h2 class="sec-title"><strong>NEWS, EVENTS</strong> &amp; FEATURES</h2>
    <div class="rule"></div>
    <div class="news-row">
      <article class="post"><div class="photo" role="img" aria-label="Exhibition stand at a maritime conference" style="background:linear-gradient(180deg,#e9eef3,#9fb2c8 50%,#1f3d6c)"><span class="date">JULY 20, 2021</span></div><h3>We attended the Maritime 2021 conference</h3><p>Lorem ipsum dolor sit amet consect</p><a class="more" href="#">LEARN MORE &rarr;</a></article>
      <article class="post"><div class="photo" role="img" aria-label="Video still of an installation engineer on site" style="background:linear-gradient(180deg,#7a6a5a,#5a4438 50%,#a0623c)"><span class="date">JULY 20, 2021</span></div><h3>Recent installation in Saudi Arabia</h3><p>Lorem ipsum dolor sit amet, consect</p><a class="more" href="#">LEARN MORE &rarr;</a></article>
      <article class="post"><div class="photo" role="img" aria-label="Product testing rig with yellow tools" style="background:linear-gradient(180deg,#cfcfc8,#3b3b38 55%,#8a8a7e)"><span class="date">JULY 20, 2021</span></div><h3>Testing our products, how we make sure that RVT solutions are fit for purpose</h3><a class="more" href="#">LEARN MORE &rarr;</a></article>
      <article class="post"><div class="photo" role="img" aria-label="Custom tensioning tool on a white background" style="background:linear-gradient(180deg,#ffffff,#e6e6e2 55%,#b8b8ae)"><span class="date">JULY 20, 2021</span></div><h3>Custom tools – when you need to make sure the fit is right</h3><a class="more" href="#">LEARN MORE &rarr;</a></article>
    </div>
  </section>

  <section class="offices">
    <div class="office" style="left:100px">
      <div class="map" role="img" aria-label="Street map of the UK office location" style="background:#eceff2"></div>
      <div class="info">
        <h3>RVT FASTENERS LIMITED<span>FOR UK, EU, EMEA &amp; WORLDWIDE</span></h3>
        <h4>MAIN OFFICE:</h4>
        <div class="line" style="padding-left:0">Binding House</div>
        <div class="line"><svg width="12" height="15" viewBox="0 0 12 15"><path d="M6 14 C2 9 1 7 1 5 a5 5 0 0 1 10 0 c0 2-1 4-5 9z" fill="var(--orange)"/></svg>4 Mill Lane Business Park<br>Elmbury, Westshire EL4 7QT<br>United Kingdom</div>
        <div class="line"><svg width="12" height="12" viewBox="0 0 12 12"><path d="M2 1 L4.5 1 L5.5 4 L4 5 C5 7 6 8 7 8.5 L8 7 L11 8 L11 10.5 C6 11 1 6 2 1z" fill="var(--orange)"/></svg>Tel: +44 (0)1632 960418</div>
      </div>
      <div class="corner"></div>
    </div>
    <div class="office" style="left:612px">
      <div class="map" role="img" aria-label="Street map of the US office location" style="background:#eceff2"></div>
      <div class="info">
        <h3>RVT FASTENERS CORP<span>FOR USA &amp; CANADA</span></h3>
        <h4>MAIN OFFICE:</h4>
        <div class="line"><svg width="12" height="15" viewBox="0 0 12 15"><path d="M6 14 C2 9 1 7 1 5 a5 5 0 0 1 10 0 c0 2-1 4-5 9z" fill="var(--orange)"/></svg>Oakridge Business Centre<br>4810 Oakridge Road, Suite 12<br>Riverton, Texas, 77000 USA</div>
        <div class="line"><svg width="12" height="12" viewBox="0 0 12 12"><path d="M2 1 L4.5 1 L5.5 4 L4 5 C5 7 6 8 7 8.5 L8 7 L11 8 L11 10.5 C6 11 1 6 2 1z" fill="var(--orange)"/></svg>Tel: 555 014 2290</div>
        <div class="line"><svg width="12" height="12" viewBox="0 0 12 12"><path d="M2 1 L4.5 1 L5.5 4 L4 5 C5 7 6 8 7 8.5 L8 7 L11 8 L11 10.5 C6 11 1 6 2 1z" fill="var(--orange)"/></svg>Toll free: 1-800 555 0147</div>
      </div>
      <div class="corner"></div>
    </div>
  </section>

  <footer class="footer">
    <div class="f-cols">
      <div class="f-col" style="padding-left:28px"><h5>HOSE CLAMPS</h5><ul><li>Grip Clip</li><li>Snapclamp</li><li>Snapclik</li><li>Air Tools</li><li>Distributed Brands</li></ul></div>
      <div class="f-col" style="padding-left:28px"><h5>HOSE CLAMPS</h5><ul><li>Flex Band</li><li>Flex Tie</li><li>Flex Protectors</li><li>Flex Saddles</li><li>Installation Tools</li></ul></div>
      <div class="f-col" style="padding-left:28px;width:236px"><h5>HOSE CLAMPS</h5><ul><li>Custom Solutions</li><li>Applications</li><li>Case Studies</li><li>Quality &amp; Testing</li><li>Facility</li><li>Contact Us</li></ul></div>
      <div class="f-col contact" style="padding-left:28px"><h5>CONTACT RVT</h5><u>Send an Email</u><br><b>UK/EU</b><br>Tel: +44 (0)1632 960418<br>Online Store<br><b>US/CA</b><br>Tel: 555 014 2290<br>Toll free: 1-800 555 0147<div class="social"><span></span><span></span><span></span></div></div>
    </div>
    <div class="f-bottom"><span>© RVT Fasteners Limited. All rights reserved</span><nav><a href="#">Sitemap</a><a href="#">Terms of Use</a><a href="#">Privacy Policy</a><a href="#">Contact Us</a></nav></div>
  </footer>

</div>
</body>
</html>
```